Business Card Design for Retail Product Line

We need a two-sided, full-color business card for a new oral care product line. The feel of the card should invoke emotions of happiness and health. It should be bright, cheerful and modern in appearance. The card should be mostly matte finish, but with elements of spot-gloss and/or raised/embossed features (print, logo, tag lines, etc.).

Target Market(s)

People who are into whole-body health, eat well and understand the importance of nutrition.

Industry/Entity Type

Health And Wellness

Contact Information for Business Card

The logo, color scheme and tag-lines have all been developed and artwork is attached. Card is to be standard-sized and should use a mix of clean, sans-serif fonts; the main font (DIN) is attached as well. The card will be used for 3 individuals and should include placeholders for:
1. Name
2. Title (for example, "CEO")
3. Business address
4. Phone number
5. Website
6. Email address

Font styles to use
Sans Serif
Other font styles liked:
• DIN font

Colors
faa54b
000000
5c5c5c
a2ce44

Requirements
Must have
• 2 sides
• Full color orange on one side
• Image of DNA leaves
• Tag line "Bright from the Root Up", on single side with orange background
• Company Logo (Plure) on same side as text (name, phone, address, etc.)
• Name, Title, Business Address, Phone Number, Website, Email address
• UPDATE: "Brisk Meadow", not "Brisk M Eadow"
Should not have
• Calligraphy
• Dark colors
• UPDATE!! Do not include "Turmeric infused toothpaste" on the business card
• UPDATE #2!! Do not include "Brisk Meadow" on the business card

```html
<!DOCTYPE html>
<html lang="en">
<head>
<meta charset="utf-8">
<title>Plure Business Card</title>
<link href="https://fonts.googleapis.com/css2?family=Barlow:wght@700&family=Open+Sans:wght@400;600&display=swap" rel="stylesheet">
<style>
  :root {
    --orange: #faa54b;
    --orange-deep: #e89a2f;
    --yellow: #f4d63e;
    --text-dark: #2b2b2b;
    --text-grey: #5c5c5c;
    --leaf-green: #a2ce44;
    --leaf-deep: #3f9a2c;
    --helix-grey: #a9a9a9;
    --card-white: #fbfbfb;
    --panel-tint: #f2f2f2;
    --page: #e6e4e1;
  }
  * { box-sizing: border-box; margin: 0; padding: 0; }
  html, body { width: 1200px; height: 900px; overflow: hidden; }
  body {
    background: var(--page);
    display: flex;
    align-items: center;
    justify-content: center;
    gap: 40px;
  }
  .card {
    width: 540px;
    height: 309px;
    position: relative;
    overflow: hidden;
    box-shadow: 0 10px 24px rgba(0,0,0,0.18);
  }

  /* Contact side */
  .card-contact {
    background: var(--card-white);
    display: flex;
  }
  .brand-area {
    width: 52%;
    display: flex;
    align-items: center;
    justify-content: center;
  }
  .brand-name {
    font-family: "Open Sans", sans-serif;
    font-weight: 600;
    font-size: 64px;
    color: var(--orange);
    letter-spacing: -1px;
  }
  .details-panel {
    width: 48%;
    background: var(--panel-tint);
    padding: 62px 20px 0 24px;
    font-family: "Open Sans", sans-serif;
    color: var(--text-dark);
    font-size: 13px;
    line-height: 1.3;
  }
  .person-name {
    color: var(--orange-deep);
    font-weight: 600;
    font-size: 15px;
  }
  .person-title { margin-bottom: 18px; }
  .address { margin-bottom: 18px; }
  .contact-list { list-style: none; }
  .contact-list li {
    display: flex;
    align-items: center;
    gap: 8px;
    margin-bottom: 2px;
  }
  .contact-icon { width: 11px; height: 11px; flex: none; }

  /* Tagline side */
  .card-tagline {
    background: linear-gradient(30deg, var(--orange-deep) 0%, var(--orange) 45%, var(--yellow) 100%);
  }
  .dna-leaves {
    position: absolute;
    left: 40px;
    top: 30px;
    width: 170px;
    height: 250px;
    border-radius: 40px 40px 20px 20px;
    background: linear-gradient(160deg, var(--leaf-green) 0%, var(--leaf-deep) 45%, var(--helix-grey) 100%);
    opacity: 0.85;
  }
  .tagline {
    position: absolute;
    left: 250px;
    top: 78px;
    width: 260px;
    font-family: "Barlow", sans-serif;
    font-weight: 700;
    font-size: 46px;
    line-height: 1.05;
    color: #ffffff;
  }
</style>
</head>
<body>
  <section class="card card-contact">
    <div class="brand-area">
      <span class="brand-name">Plure</span>
    </div>
    <div class="details-panel">
      <p class="person-name">Maren Holt</p>
      <p class="person-title">Managing Director</p>
      <p class="address">48 Orchard Lane<br>Greenfield, 560231.</p>
      <ul class="contact-list">
        <li>
          <svg class="contact-icon" viewBox="0 0 12 12"><path d="M2.5 1 L4.5 1 L5.2 3.4 L4 4.4 C4.6 5.8 6.2 7.4 7.6 8 L8.6 6.8 L11 7.5 L11 9.5 C11 10.4 10.2 11 9.3 11 C5 10.6 1.4 7 1 2.7 C1 1.8 1.6 1 2.5 1 Z" fill="var(--orange-deep)"/></svg>
          <span>055-246 810 357</span>
        </li>
        <li>
          <svg class="contact-icon" viewBox="0 0 12 12"><rect x="0.5" y="2" width="11" height="8" rx="1" fill="var(--orange-deep)"/><path d="M1 2.6 L6 6.6 L11 2.6" stroke="#fff" stroke-width="1" fill="none"/></svg>
          <span>hello@plurecare.com</span>
        </li>
        <li>
          <svg class="contact-icon" viewBox="0 0 12 12"><circle cx="6" cy="6" r="5.5" fill="var(--orange-deep)"/><path d="M0.5 6 H11.5 M6 0.5 C3.5 3 3.5 9 6 11.5 M6 0.5 C8.5 3 8.5 9 6 11.5" stroke="#fff" stroke-width="0.7" fill="none"/></svg>
          <span>www.plurecare.com</span>
        </li>
      </ul>
    </div>
  </section>

  <section class="card card-tagline">
    <div class="dna-leaves" role="img" aria-label="Green leaves growing from a grey and green DNA double helix"></div>
    <p class="tagline">Bright from<br>the root up</p>
  </section>
</body>
</html>
```